Blow Dry Bar Business Cards

These cards must be eye catching and modern.
You must be willing to work fast and make changes.

Winner will be offered other projects

Files 1 THIS IS THE STYLE CARDS I AM INTRESTED IN!!!
Please be creative, I am paying for my own eye catching design. I need files to be nexa press ready.

COLORS THAT ARE PAINTED INSIDE MY SHOP:
- - - http://www.quorvelpaint.example/en/explore-colors/painter/color-selector.html?colors=4007-3C

- - - http://www.brandivex.example/color/paint-colors/hidden-corridor-d58-2

I want the business cards sleek and modern if you use the logo please correct imperfections. I added the part that says Blow Dry Bar (see website).
Do not be afraid to separate the blow dryer from the name to make the cards look like the file with the pink elephant.

SHOULD INCLUDE
*Blow Dryer (we are a blow dry bar not a salon we do not cut or color so do not include sheers of any kind)
*BUSINESS NAME: Simply Swept Upward - Blow Dry Bar (PLEASE SEE MY WEBSITE)
* Website: SIMPLYSWEPTUPWARD.EXAMPLE
*Phone number (555) 014-2763
Updates

Nexa press said it can be submitted in JPG

http://www.brandivex.example/color/paint-colors/hidden-corridor-d58-2 http://www.quorvelpaint.example/en/explore-colors/painter/color-selector.html?colors=4007-3C ^^^^ These links will take you to the color paint that is painted inside my shop.

Target Market(s)

AGES 18 - 55 WOMEN
HIGH END MARKET

Industry/Entity Type

Salon

Requirements
Must have
• SEE COLOR EXAMPLE FILE
BLOW DRYER
UNIQUE
I LIKE THE CARD WITH THE PINK ELEPHANT THE BEST
Nice to have
• BE AS CREATIVE AND MODERN AS POSSIBLE DO NOT COPY ANY OF THE CARDS BELOW.
Should not have
• SCISSORS
PINK

```html
<!DOCTYPE html>
<html lang="en">
<head>
<meta charset="utf-8">
<title>Simply Swept Upward – Blow Dry Bar Business Cards</title>
<link href="https://fonts.googleapis.com/css2?family=Josefin+Sans:wght@300;400&display=swap" rel="stylesheet">
<style>
  :root {
    --backdrop: #ece9e3;
    --card-dark: #2b2b2c;
    --card-mid: #3e3e40;
    --gold: #e6d7a6;
    --cream: #e9dcb4;
    --ink: #2a2824;
  }
  * { box-sizing: border-box; margin: 0; padding: 0; }
  html, body { width: 1200px; height: 885px; overflow: hidden; }
  body {
    background: var(--backdrop);
    font-family: "Josefin Sans", sans-serif;
    font-weight: 300;
    display: flex;
    flex-direction: column;
    align-items: center;
    justify-content: center;
    gap: 50px;
  }
  .card {
    position: relative;
    width: 640px;
    height: 366px;
    border-radius: 16px;
    overflow: hidden;
    color: var(--gold);
    box-shadow: 0 6px 18px rgba(0,0,0,.25);
  }
  .card-texture {
    position: absolute; inset: 0;
    background: radial-gradient(ellipse at 45% 35%, var(--card-mid), var(--card-dark) 75%);
  }
  /* Info side */
  .top-rule {
    position: absolute; left: 0; right: 0; top: 42px;
    height: 1px; background: var(--gold);
  }
  .title {
    position: absolute; left: 40px; top: 74px;
    font-size: 54px; letter-spacing: 1px; white-space: nowrap;
  }
  .title-rule {
    position: absolute; left: 372px; right: 0; top: 112px;
    height: 1px; background: var(--gold);
  }
  .owners {
    position: absolute; left: 250px; top: 150px;
    font-size: 22px; display: flex; align-items: center; gap: 14px;
  }
  .owners::before {
    content: ""; width: 110px; height: 1px; background: var(--gold);
    margin-left: -124px;
  }
  .contact {
    position: absolute; left: 250px; top: 196px;
    list-style: none; font-size: 17px; line-height: 30px;
    letter-spacing: .5px; text-transform: uppercase;
  }
  .address-band {
    position: absolute; left: 0; right: 0; bottom: 0; height: 44px;
    background: var(--cream); color: var(--ink);
    font-size: 17px; letter-spacing: .5px; text-transform: uppercase;
    display: flex; align-items: center; padding-left: 40px;
  }
  /* Brand side */
  .brand {
    position: absolute; left: 0; right: 0; top: 110px;
    display: flex; align-items: center; justify-content: center; gap: 22px;
  }
  .brand-name { font-size: 50px; font-weight: 400; white-space: nowrap; }
  .brand-dot { width: 40px; height: 40px; border-radius: 50%; background: var(--gold); }
  .site {
    position: absolute; left: 0; right: 0; top: 210px; text-align: center;
    font-size: 18px; letter-spacing: 1px;
  }
  .site-rule {
    position: absolute; left: 270px; width: 100px; top: 262px;
    height: 1px; background: var(--gold);
  }
</style>
</head>
<body>
  <section class="card card-info">
    <div class="card-texture" role="img" aria-label="Dark charcoal damask pattern background"></div>
    <div class="top-rule"></div>
    <h1 class="title">Blow Dry Bar</h1>
    <div class="title-rule"></div>
    <p class="owners">Marisol&amp;Teva</p>
    <ul class="contact">
      <li>(555) 014-2763</li>
      <li>SIMPLYSWEPTUPWARD.EXAMPLE</li>
      <li>INFO@SIMPLYSWEPTUPWARD.EXAMPLE</li>
    </ul>
    <div class="address-band">208 Heron Bend Lane Suite 4 Fairhollow, Texas 75099</div>
  </section>

  <section class="card card-brand">
    <div class="card-texture" role="img" aria-label="Dark charcoal damask pattern background"></div>
    <div class="brand">
      <span class="brand-name">Simply Swept Upward</span>
      <span class="brand-dot"></span>
    </div>
    <p class="site">SIMPLYSWEPTUPWARD.EXAMPLE</p>
    <div class="site-rule"></div>
  </section>
</body>
</html>
```